Harborline Renewal Business Card Design

Professional and clean design. The design colors should flow with the logo. Two-sided card with the website on the back which is:

www.HarborlineRenewal.example.

"Specializing in Water Damage Restoration"

On the front I need the name, email, phone, and logo.

Name: Darnell Quisby
Email: Darnell@HarborlineRenewal.example
Phone: 555-318-2046 for now

I only have the Preview and Thumbnail right now but should have the source files uploaded within a day or two.

Target Market(s)

Flood victims, home owners with water damage from busted pipes etc...

Industry/Entity Type

Business

Contact Information for Business Card

Name: Darnell Quisby

Font styles to use
Serif
Sans Serif

Requirements
Must have
• Business Card Details Info

```html
<!DOCTYPE html>
<html lang="en">
<head>
<meta charset="utf-8">
<title>Harborline Renewal Business Card</title>
<link rel="stylesheet" href="https://fonts.googleapis.com/css2?family=Cinzel:wght@600&family=Ubuntu:wght@400;700&display=swap">
<style>
  :root {
    --page: #ecebe8;
    --white: #ffffff;
    --blue: #2597d6;
    --blue-light: #56bdea;
    --blue-tab: #8fd3f2;
    --shadow: rgba(0, 0, 0, 0.18);
  }
  * { box-sizing: border-box; margin: 0; padding: 0; }
  html, body {
    width: 1200px; height: 1000px; overflow: hidden;
    background: var(--page);
  }
  .sheet { position: relative; width: 1200px; height: 1000px; }
  .card {
    position: absolute; left: 220px; width: 760px; height: 434px;
    border-radius: 26px; overflow: hidden; background: var(--white);
    box-shadow: 0 10px 26px var(--shadow);
  }
  .card--back { top: 38px; }
  .card--front { top: 528px; }
  .card svg.bands { position: absolute; inset: 0; }

  .brand {
    position: absolute; display: flex; flex-direction: column; align-items: center;
    font-family: "Cinzel", serif; font-weight: 600; letter-spacing: 2px;
    line-height: 1.15; text-align: center; white-space: nowrap;
  }
  .brand__dot { border-radius: 50%; flex: none; margin-bottom: 10px; }

  .card--back .brand {
    left: 0; right: 0; top: 50px;
    font-size: 40px; color: var(--blue);
  }
  .card--back .brand__dot { background: var(--blue); width: 64px; height: 64px; }

  .tagline {
    position: absolute; left: 0; right: 0; top: 290px; text-align: center;
    font-family: "Ubuntu", sans-serif; font-size: 17px; letter-spacing: 1px;
    color: var(--white);
  }
  .website {
    position: absolute; left: 0; right: 0; top: 352px;
    display: flex; justify-content: center; align-items: center; gap: 12px;
    font-family: "Ubuntu", sans-serif; font-size: 21px; letter-spacing: 0.5px;
    color: var(--white);
  }

  .card--front .brand {
    left: 20px; width: 300px; top: 118px;
    font-size: 30px; color: var(--white);
  }
  .card--front .brand__dot { background: var(--white); width: 56px; height: 56px; }

  .person {
    position: absolute; left: 372px; right: 22px; top: 150px;
    font-family: "Ubuntu", sans-serif; color: var(--blue);
  }
  .person__name {
    font-size: 34px; font-weight: 700; letter-spacing: 0.5px;
    text-align: center; margin-bottom: 16px;
  }
  .contact {
    position: relative; display: flex; align-items: center; gap: 10px;
    height: 36px; font-size: 18px; white-space: nowrap;
  }
  .contact__tab {
    position: absolute; left: -40px; width: 60px; height: 12px;
    background: var(--blue-tab); border-radius: 0 6px 6px 0;
  }
  .contact__mark {
    position: relative; width: 28px; height: 28px; border-radius: 50%;
    border: 2px solid var(--blue); background: var(--white);
    display: flex; align-items: center; justify-content: center;
    font-size: 15px; font-weight: 700; flex: none;
  }
</style>
</head>
<body>
<main class="sheet">

  <section class="card card--back" aria-label="Card back">
    <svg class="bands" width="760" height="434" viewBox="0 0 760 434" aria-hidden="true">
      <rect x="0" y="276" width="760" height="48" fill="var(--blue-light)"/>
      <rect x="0" y="324" width="760" height="110" fill="var(--blue)"/>
    </svg>
    <div class="brand"><span class="brand__dot"></span><span>Harborline</span><span>Renewal</span></div>
    <p class="tagline">*Specializing in Water Damage Restoration*</p>
    <p class="website">
      <svg width="22" height="22" viewBox="0 0 22 22" aria-hidden="true">
        <circle cx="11" cy="11" r="9" fill="none" stroke="var(--white)" stroke-width="2"/>
        <path d="M2 11h18M11 2c-4 5-4 13 0 18M11 2c4 5 4 13 0 18" fill="none" stroke="var(--white)" stroke-width="1.5"/>
      </svg>
      www.HarborlineRenewal.example
    </p>
  </section>

  <section class="card card--front" aria-label="Card front">
    <svg class="bands" width="760" height="434" viewBox="0 0 760 434" aria-hidden="true">
      <polygon points="0,0 378,0 318,434 0,434" fill="var(--blue)"/>
    </svg>
    <div class="brand"><span class="brand__dot"></span><span>Harborline</span><span>Renewal</span></div>
    <div class="person">
      <h1 class="person__name">Darnell Quisby</h1>
      <p class="contact"><span class="contact__tab"></span><span class="contact__mark">M</span>Darnell@HarborlineRenewal.example</p>
      <p class="contact"><span class="contact__tab"></span><span class="contact__mark">E</span>555-318-2046</p>
    </div>
  </section>

</main>
</body>
</html>
```